Global (re)insurance broker needs a business card design

We need a classic business card for our company that is headquartered in SG, with offices in Malaysia and Dubai. We specialise in insurance and reinsurance broking and consultancy for our global clients.

```html
<!DOCTYPE html>
<html lang="en">
<head>
<meta charset="utf-8">
<title>Meridane Business Card</title>
<link rel="stylesheet" href="https://fonts.googleapis.com/css2?family=Montserrat:wght@500;700&family=Open+Sans:wght@400&display=swap">
<style>
  :root {
    --stage: #2b2b2f;
    --card: #151515;
    --brand-blue: #2a4ea3;
    --brand-green: #c4dfb6;
    --text-light: #f2f2f2;
  }
  * { margin: 0; padding: 0; box-sizing: border-box; }
  html, body { width: 1200px; height: 947px; overflow: hidden; background: var(--stage); }
  .stage { position: relative; width: 1200px; height: 947px; }
  .card {
    position: absolute;
    left: 290px;
    width: 620px;
    height: 354px;
    background: var(--card);
    border-radius: 22px;
    overflow: hidden;
  }
  .card--front { top: 80px; }
  .card--back { top: 512px; }

  .wordmark {
    font-family: "Montserrat", sans-serif;
    font-weight: 700;
    letter-spacing: 0.04em;
    color: var(--brand-green);
  }
  .card--front .wordmark {
    position: absolute;
    left: 0; right: 0; top: 50%;
    transform: translateY(-50%);
    text-align: center;
    font-size: 84px;
  }
  .card--back .wordmark {
    position: absolute;
    left: 44px; top: 128px;
    font-size: 46px;
  }

  .holder {
    position: absolute;
    right: 44px; top: 36px;
    text-align: right;
    padding-right: 0;
  }
  .holder__name {
    font-family: "Montserrat", sans-serif;
    font-weight: 700;
    font-size: 24px;
    color: var(--brand-blue);
    line-height: 1.1;
  }
  .holder__title {
    font-family: "Open Sans", sans-serif;
    font-size: 15px;
    color: var(--text-light);
    margin-top: 4px;
  }
  .holder-bar {
    position: absolute;
    right: 0; top: 34px;
    width: 14px; height: 50px;
    background: var(--brand-blue);
  }

  .address, .contacts {
    position: absolute;
    left: 44px;
    font-family: "Open Sans", sans-serif;
    font-size: 14px;
    line-height: 1.45;
    color: var(--text-light);
  }
  .address { top: 208px; }
  .contacts { top: 280px; list-style: none; }
  .contacts li { display: flex; align-items: center; gap: 8px; }
  .contacts svg { width: 12px; height: 12px; fill: var(--brand-blue); flex: none; }
</style>
</head>
<body>
<main class="stage">
  <section class="card card--front" aria-label="Card front">
    <div class="wordmark">MERIDANE</div>
  </section>

  <section class="card card--back" aria-label="Card back">
    <div class="holder">
      <div class="holder__name">Lena Howard</div>
      <div class="holder__title">Chief Operating Officer</div>
    </div>
    <div class="holder-bar"></div>

    <div class="wordmark">MERIDANE</div>

    <address class="address" style="font-style:normal">
      24 Harbour Street,<br>
      Quayside Tower #08-04,<br>
      Singapore 049512
    </address>

    <ul class="contacts">
      <li>
        <svg viewBox="0 0 24 24" aria-hidden="true"><path d="M6.6 10.8a15.1 15.1 0 0 0 6.6 6.6l2.2-2.2c.3-.3.7-.4 1-.2 1.1.4 2.3.6 3.6.6.6 0 1 .4 1 1V20c0 .6-.4 1-1 1A17 17 0 0 1 3 4c0-.6.4-1 1-1h3.5c.6 0 1 .4 1 1 0 1.3.2 2.5.6 3.6.1.3 0 .7-.2 1z"/></svg>
        +65 9123 4560
      </li>
      <li>
        <svg viewBox="0 0 24 24" aria-hidden="true"><path d="M2 5h20v14H2z M2 5l10 8 10-8" /></svg>
        lena@meridane.com
      </li>
      <li>
        <svg viewBox="0 0 24 24" aria-hidden="true"><circle cx="12" cy="12" r="10"/></svg>
        www.meridane.com
      </li>
    </ul>
  </section>
</main>
</body>
</html>
```